Website for Life Strategies business

We need a website to present our video, audio and print content to subcribers at Bright Summit Mentors. We will offer a team of coaches who can help people breakthrough the barriers that keep them from reaching their physical, spiritual, financial, leadership and relationship goals.

Target Market(s)

Anyone who needs help with strategies to take their life to a new level of success.

Industry/Entity Type

Life Coaching

Logo Text

Bright Summit Mentors

Number of Pages Required

5+ page

Colors

Designer to choose colors to be used in the design.

Requirements
Must have
• The ability to present content as a package that includes Word Documents, videos and audio content as well as to be able to display books for sale. Each week their would be a new package for subscribers to access. It should provide the ability for subscribers to comment on the material and share how their lives were changed by the content. Should also include a shop page to offer merchandise for sale.
Nice to have
• Not sure
Should not have
• Not sure

```html
<!DOCTYPE html>
<html lang="en">
<head>
<meta charset="utf-8">
<title>Bright Summit Mentors</title>
<link rel="stylesheet" href="https://fonts.googleapis.com/css2?family=Poppins:wght@400;500;600&family=Open+Sans:wght@400;600;700&family=Oswald:wght@500&display=swap">
<style>
:root{
  --brand-blue:#2c3f93;
  --band-blue:#2b5f98;
  --wave-green:#8cc63f;
  --ink:#333333;
  --muted:#6b6b6b;
  --date-blue:#2c5aa0;
  --footer-bg:#1d1d1d;
  --footer-text:#e6e6e6;
  --card-bg:#f7f7f7;
  --icon-bg:#2f2f2f;
  --rule:#e3e3e3;
}
*{box-sizing:border-box;margin:0;padding:0}
html,body{width:1200px;height:2635px;overflow:hidden;background:#fff}
body{position:relative;font-family:"Open Sans",Arial,sans-serif;color:var(--ink)}
.abs{position:absolute}
/* header */
.site-header{left:0;top:0;width:1200px;height:100px;background:#fff;box-shadow:0 2px 4px rgba(0,0,0,.12);z-index:2}
.brand{left:97px;top:28px;font-family:"Oswald",sans-serif;font-weight:500;font-size:33px;color:var(--ink);letter-spacing:-.5px}
.nav a{position:absolute;top:43px;font-size:13px;font-weight:600;color:var(--ink);text-decoration:none;letter-spacing:.5px}
.nav a.active{color:var(--brand-blue)}
.nav-underline{left:594px;top:96px;width:34px;height:3px;background:var(--brand-blue)}
/* hero */
.hero{left:0;top:100px;width:1200px;height:529px;background:linear-gradient(180deg,#27303f 0%,#5a6a86 30%,#c98a6a 55%,#4b4f66 68%,#2a2f3e 100%)}
.hero-title{left:97px;top:285px;font-family:"Poppins",sans-serif;font-weight:600;font-size:38px;line-height:44px;color:#fff}
.hero-sub{left:97px;top:378px;font-size:14px;font-weight:600;line-height:20px;color:#fff}
.hero-dots{left:100px;top:440px;display:flex;gap:8px}
.hero-dots span{width:10px;height:10px;border-radius:50%;background:#fff}
.hero-dots span.on{width:16px;height:16px;margin-top:-3px;background:transparent;border:3px solid #fff;box-shadow:inset 0 0 0 2px #555;}
/* welcome */
.welcome-media{left:112px;top:722px;width:464px;height:297px;border:4px solid #e6e6e6;background:linear-gradient(135deg,#c9d6e0,#8f9fb0 50%,#e7e2da)}
.play{left:318px;top:839px;width:54px;height:54px;border-radius:50%;border:3px solid rgba(255,255,255,.85);background:rgba(0,0,0,.25)}
.welcome-title{left:625px;top:728px;font-family:"Poppins",sans-serif;font-size:33px;line-height:38px;color:var(--ink);font-weight:400}
.welcome-text{left:625px;top:820px;width:460px;font-size:12px;line-height:19px;color:#555}
.welcome-list{left:625px;top:922px;list-style:none;font-size:12px;line-height:22px;color:#555}
.welcome-list li{position:relative;padding-left:22px}
.welcome-list li::before{content:"";position:absolute;left:2px;top:7px;width:8px;height:8px;border-radius:50%;background:#333}
/* coaches band */
.coaches-band{left:0;top:1085px;width:1200px;height:616px}
.coaches-title{left:0;top:1188px;width:1200px;text-align:center;font-family:"Poppins",sans-serif;font-size:33px;color:#fff}
.coach-card{top:1335px;width:241px;height:260px;background:var(--card-bg);text-align:center}
.coach-icon{position:absolute;left:71px;top:-49px;width:98px;height:98px;border-radius:50%;background:var(--icon-bg);border:4px solid #e9e9e9;display:flex;align-items:center;justify-content:center}
.coach-name{position:absolute;left:0;top:80px;width:100%;font-family:"Poppins",sans-serif;font-size:20px;color:#444}
.coach-text{position:absolute;left:26px;top:114px;width:189px;font-size:12px;line-height:20px;color:#666}
.coach-more{position:absolute;left:0;top:218px;width:100%;height:42px;border-top:1px solid var(--rule);font-size:11px;line-height:42px;color:#555;letter-spacing:.5px}
/* news */
.section-title{font-family:"Poppins",sans-serif;font-size:28px;color:var(--ink)}
.news-thumb{left:98px;width:215px;height:141px}
.news-heading{left:334px;font-family:"Poppins",sans-serif;font-size:16px;color:#444}
.news-date{left:336px;font-size:12px;font-style:italic;font-weight:600;color:var(--date-blue)}
.news-text{left:334px;width:400px;font-size:12px;line-height:20px;color:#666}
.news-rule{left:334px;width:439px;height:1px;background:var(--rule)}
.goal-photo{left:799px;top:1857px;width:303px;height:179px;border:3px solid #e6e6e6;background:linear-gradient(135deg,#e8e4dc,#c4b9a6 50%,#7b8fa3)}
.goal-heading{left:799px;top:2054px;font-family:"Poppins",sans-serif;font-size:16px;color:#444}
.goal-text{left:799px;top:2088px;width:300px;font-size:12px;line-height:20px;color:#666}
.goal-link{left:799px;top:2163px;font-size:13px;color:#333;letter-spacing:.3px}
/* footer */
.site-footer{left:0;top:2272px;width:1200px;height:363px;background:var(--footer-bg);color:var(--footer-text)}
.foot-head{font-family:"Poppins",sans-serif;font-size:16px;font-weight:500;color:#fff;letter-spacing:.3px}
.foot-row{left:132px;font-size:13px;line-height:20px}
.foot-icon{left:97px}
.foot-note{left:427px;top:2368px;width:300px;font-size:11px;line-height:18px;color:#ddd}
.foot-input{left:427px;top:2421px;width:285px;height:40px;background:#fff;font-size:11px;color:#555;padding:12px 14px}
.foot-btn{left:427px;top:2472px;width:98px;height:41px;background:var(--brand-blue);color:#fff;font-size:12px;font-weight:700;text-align:center;line-height:41px}
.quick-links{left:808px;top:2370px;list-style:none;font-size:12px;line-height:24px}
.social-item{left:1001px;display:flex;align-items:center;gap:10px;font-size:13px}
.social-item span.dot{width:27px;height:27px;border-radius:50%;border:2px solid #ddd}
.copyright{left:0;top:2592px;width:1200px;text-align:center;font-size:11px;color:#ddd}
</style>
</head>
<body>

<header class="abs site-header">
  <div class="abs brand">Bright Summit Mentors</div>
  <nav class="nav">
    <a class="active" style="left:594px">HOME</a>
    <a style="left:682px">ABOUT US</a>
    <a style="left:794px">OUR SERVICES</a>
    <a style="left:931px">BLOG</a>
    <a style="left:1008px">CONTACT US</a>
  </nav>
  <div class="abs nav-underline"></div>
</header>

<section class="abs hero" role="img" aria-label="Silhouette of a person meditating by the sea at sunset"></section>
<h1 class="abs hero-title">BRIGHT SUMMIT<br>MENTORS.</h1>
<p class="abs hero-sub">Sed ut perspiciatis unde omnis iste natus error sit<br>voluptatem accusantium doloremque</p>
<div class="abs hero-dots"><span class="on"></span><span></span><span></span><span></span></div>

<div class="abs welcome-media" role="img" aria-label="Video still of a coach meeting a client at a desk"></div>
<svg class="abs" style="left:318px;top:839px" width="54" height="54" viewBox="0 0 54 54">
  <circle cx="27" cy="27" r="25" fill="rgba(0,0,0,.25)" stroke="rgba(255,255,255,.85)" stroke-width="3"/>
  <path d="M22 17 L37 27 L22 37 Z" fill="rgba(255,255,255,.9)"/>
</svg>
<h2 class="abs welcome-title">WELCOME TO<br>BRIGHT SUMMIT MENTORS</h2>
<p class="abs welcome-text">Sed ut perspiciatis unde omnis iste natus error sit voluptatem accusantium doloremque laudantium, totam rem aperiam, eaque ipsa quae ab illo inventore veritatis et quasi architecto beatae vitae dicta sunt explicabo. Nemo enim ipsam voluptatem quia voluptas sit aspernatur aut odit aut fugit, sed quia consequuntur</p>
<ul class="abs welcome-list">
  <li>Nemo enim ipsam voluptatem quia</li>
  <li>Ut enim ad minima veniam, quis nostrum</li>
  <li>Quis autem vel eum iure reprehenderit qui in ea voluptate</li>
  <li>Neque porro quisquam est,</li>
</ul>

<svg class="abs coaches-band" viewBox="0 0 1200 616" width="1200" height="616" role="img" aria-label="Misty lakeside forest backdrop in blue">
  <defs>
    <linearGradient id="bandFill" x1="0" y1="0" x2="0" y2="1">
      <stop offset="0" stop-color="#2f6aa6"/>
      <stop offset=".5" stop-color="#2b5f98"/>
      <stop offset="1" stop-color="#26558a"/>
    </linearGradient>
  </defs>
  <path d="M0 28 C180 8 330 0 480 14 C640 30 820 44 1000 22 C1100 12 1160 8 1200 12 L1200 616 L0 616 Z" fill="url(#bandFill)"/>
  <path d="M0 28 C180 8 330 0 480 14 C640 30 820 44 1000 22 C1100 12 1160 8 1200 12" fill="none" stroke="var(--wave-green)" stroke-width="4"/>
</svg>
<h2 class="abs coaches-title">Our Coaches</h2>

<div class="abs coach-card" style="left:98px">
  <div class="coach-icon"><svg width="44" height="44" viewBox="0 0 44 44" fill="none" stroke="#fff" stroke-width="3" stroke-linecap="round"><path d="M22 40V18M22 28l-9-7M22 24l9-7"/><circle cx="11" cy="18" r="4" fill="#fff"/><circle cx="33" cy="14" r="4" fill="#fff"/><circle cx="22" cy="9" r="4" fill="#fff"/></svg></div>
  <div class="coach-name">Physical</div>
  <p class="coach-text">Sed ut perspiciatis unde omnis iste natus error sit voluptatem accusantium doloremque laudantium, totam rem aperiam, eaque ipsa quae</p>
  <div class="coach-more">READ MORE &nbsp;↘</div>
</div>
<div class="abs coach-card" style="left:351px">
  <div class="coach-icon"><svg width="48" height="48" viewBox="0 0 48 48" fill="none" stroke="#fff" stroke-width="3"><circle cx="24" cy="24" r="13"/><circle cx="24" cy="24" r="4" fill="#fff"/><path d="M24 4v40M4 24h40M10 10l28 28M38 10L10 38"/></svg></div>
  <div class="coach-name">Spiritual</div>
  <p class="coach-text">Sed ut perspiciatis unde omnis iste natus error sit voluptatem accusantium doloremque laudantium, totam rem aperiam, eaque ipsa quae</p>
  <div class="coach-more">READ MORE &nbsp;↘</div>
</div>
<div class="abs coach-card" style="left:606px">
  <div class="coach-icon"><svg width="46" height="46" viewBox="0 0 46 46"><ellipse cx="23" cy="28" rx="16" ry="12" fill="#fff"/><rect x="12" y="36" width="5" height="6" fill="#fff"/><rect x="29" y="36" width="5" height="6" fill="#fff"/><circle cx="23" cy="10" r="6" fill="#fff"/></svg></div>
  <div class="coach-name">Financial</div>
  <p class="coach-text">Sed ut perspiciatis unde omnis iste natus error sit voluptatem accusantium doloremque laudantium, totam rem aperiam, eaque ipsa quae</p>
  <div class="coach-more">READ MORE &nbsp;↘</div>
</div>
<div class="abs coach-card" style="left:861px">
  <div class="coach-icon"><svg width="50" height="44" viewBox="0 0 50 44" fill="#fff"><circle cx="25" cy="11" r="7"/><path d="M14 40c0-12 5-18 11-18s11 6 11 18z"/><circle cx="10" cy="17" r="5"/><path d="M2 40c0-9 3-14 8-14s7 4 7 8v6z"/><circle cx="40" cy="17" r="5"/><path d="M48 40c0-9-3-14-8-14s-7 4-7 8v6z"/></svg></div>
  <div class="coach-name">Leadership</div>
  <p class="coach-text">Sed ut perspiciatis unde omnis iste natus error sit voluptatem accusantium doloremque laudantium, totam rem aperiam, eaque ipsa quae</p>
  <div class="coach-more">READ MORE &nbsp;↘</div>
</div>

<h2 class="abs section-title" style="left:97px;top:1786px">LATEST NEWS</h2>
<div class="abs news-thumb" style="top:1857px;background:linear-gradient(135deg,#d7dfe6,#7d96ad 60%,#3d5870)" role="img" aria-label="Team working together at a laptop"></div>
<h3 class="abs news-heading" style="top:1848px">Sed ut perspiciatis unde omnis iste natus</h3>
<div class="abs news-date" style="top:1882px">JAN 15, 2017</div>
<p class="abs news-text" style="top:1910px">Sed ut perspiciatis unde omnis iste natus error sit voluptatem accusantium doloremque laudantium, totam rem aperiam, eaque ipsa quae ab illo inventore veritatis et quasi</p>
<div class="abs news-rule" style="top:1998px"></div>
<div class="abs news-thumb" style="top:2038px;background:linear-gradient(135deg,#e4d8c6,#9a7f63 55%,#3e3a38)" role="img" aria-label="Woman sitting at a desk in a bright office"></div>
<h3 class="abs news-heading" style="top:2030px">Sed ut perspiciatis unde omnis iste natus</h3>
<div class="abs news-date" style="top:2064px">JAN 15, 2017</div>
<p class="abs news-text" style="top:2092px">Sed ut perspiciatis unde omnis iste natus error sit voluptatem accusantium doloremque laudantium, totam rem aperiam, eaque ipsa quae ab illo inventore veritatis</p>
<div class="abs news-rule" style="top:2179px"></div>

<h2 class="abs section-title" style="left:799px;top:1786px">RELATIONSHIP GOALS</h2>
<div class="abs goal-photo" role="img" aria-label="Two colleagues talking across a table"></div>
<h3 class="abs goal-heading">Sed ut perspiciatis unde omnis iste</h3>
<p class="abs goal-text">Sed ut perspiciatis unde omnis iste natus error sit voluptatem accusantium doloremque laudantium, totam rem aperiam, eaque ipsa quae</p>
<div class="abs goal-link">CLICK HERE &nbsp;➜</div>

<footer class="abs site-footer"></footer>
<h4 class="abs foot-head" style="left:97px;top:2330px">CONTACT US</h4>
<svg class="abs foot-icon" style="top:2384px" width="18" height="22" viewBox="0 0 18 22" fill="none" stroke="#ddd" stroke-width="2"><path d="M9 21s7-7 7-12A7 7 0 0 0 2 9c0 5 7 12 7 12z"/><circle cx="9" cy="9" r="2.5"/></svg>
<div class="abs foot-row" style="top:2375px">Bright Summit Mentors<br>4820 LM, Alder Bay The Netherlands.</div>
<svg class="abs foot-icon" style="top:2427px" width="18" height="18" viewBox="0 0 18 18" fill="none" stroke="#ddd" stroke-width="1.8"><path d="M4 1l3 4-2 2c1 2 3 4 5 5l2-2 4 3-2 3C8 16 2 10 1 4z"/></svg>
<div class="abs foot-row" style="top:2425px">Phone : &nbsp;900 1234 5670</div>
<svg class="abs foot-icon" style="top:2461px" width="20" height="14" viewBox="0 0 20 14" fill="none" stroke="#ddd" stroke-width="1.6"><rect x="1" y="1" width="18" height="12"/><path d="M1 1l9 7 9-7"/></svg>
<div class="abs foot-row" style="top:2458px">info@brightsummitmentors.com</div>

<h4 class="abs foot-head" style="left:427px;top:2326px">SIGN UP TO RECEIVE EMAIL</h4>
<p class="abs foot-note">Excepteur sint occaecat cupidatat non proident, sunt in culpa qui Nemo enim ipsam voluptatem</p>
<div class="abs foot-input">Enter Name</div>
<div class="abs foot-btn">SUBSCRIBE</div>

<h4 class="abs foot-head" style="left:808px;top:2326px">QUICK LINKS</h4>
<ul class="abs quick-links">
  <li>Home</li><li>About Us</li><li>Our Services</li><li>Consultancy</li><li>Blog</li><li>Contact Us</li>
</ul>

<h4 class="abs foot-head" style="left:1001px;top:2326px">SOCIAL</h4>
<div class="abs social-item" style="top:2370px"><span class="dot"></span>Friends Page</div>
<div class="abs social-item" style="top:2406px"><span class="dot"></span>Short Posts</div>
<div class="abs social-item" style="top:2442px"><span class="dot"></span>Circles</div>
<div class="abs social-item" style="top:2478px"><span class="dot"></span>Video Channel</div>

<p class="abs copyright">Copyright © Bright Summit Mentors 2017. All rights reserved.</p>

</body>
</html>
```